Lumavento business card

We need a modern business card - With our 4 colors - See web: www.lumavento.dk

I have attached logo and som old business Cards we have - Lets Make the new ones shine...:-) -

Industry/Entity Type

Business

Requirements
Must have
• the logo with lumavento only,

```html
<!DOCTYPE html>
<html lang="da">
<head>
<meta charset="utf-8">
<title>Lumavento – visitkort</title>
<link rel="stylesheet" href="https://fonts.googleapis.com/css2?family=Arimo:wght@400;700&display=swap">
<style>
  :root {
    --lime: #8cc63f;
    --orange: #f0923a;
    --magenta: #e0399b;
    --purple: #7b3596;
    --ink: #231f20;
    --paper: #ffffff;
    --text-light: #f2f2f2;
    --stage: #e6e6e4;
  }
  * { margin: 0; padding: 0; box-sizing: border-box; }
  html, body { width: 1200px; height: 950px; overflow: hidden; }
  body {
    background: var(--stage);
    font-family: "Arimo", Arial, sans-serif;
    position: relative;
  }
  .card {
    position: absolute;
    left: 260px;
    width: 680px;
    height: 400px;
    border-radius: 6px;
    overflow: hidden;
    box-shadow: 0 6px 18px rgba(0,0,0,0.18);
  }

  /* Front */
  .card-front { top: 60px; background: var(--paper); }
  .brand {
    position: absolute;
    left: 0; right: 0; top: 160px;
    display: flex; flex-direction: column; align-items: center;
  }
  .brand-name {
    display: flex; align-items: center; gap: 12px;
    font-weight: 700;
    font-size: 34px;
    color: var(--ink);
  }
  .brand-dot { width: 22px; height: 22px; border-radius: 50%; background: var(--lime); }
  .brand-tagline {
    font-size: 15px; color: var(--ink); margin-top: 14px;
  }

  /* Back */
  .card-back { top: 490px; background: var(--ink); }
  .back-disc { position: absolute; inset: 0; }
  .colour-tabs {
    position: absolute; left: 0; top: 150px;
    width: 16px; display: flex; flex-direction: column;
  }
  .colour-tabs span { height: 52px; border-radius: 0 6px 6px 0; margin-bottom: 3px; }
  .tab-orange { background: var(--orange); }
  .tab-lime { background: var(--lime); }
  .tab-magenta { background: var(--magenta); }
  .tab-purple { background: var(--purple); }

  .contact {
    position: absolute; left: 52px; top: 138px;
    color: var(--text-light); font-size: 17px; line-height: 23px;
  }
  .contact-name { color: var(--lime); font-weight: 700; font-size: 24px; line-height: 30px; }
  .contact-title { margin-bottom: 12px; }
  .contact-lines { list-style: none; margin-top: 4px; }
  .contact-lines li { display: flex; align-items: center; gap: 10px; }
  .contact-lines svg { width: 15px; height: 15px; flex: none; }
</style>
</head>
<body>

<section class="card card-front" aria-label="Visitkort forside">
  <div class="brand">
    <div class="brand-name"><span class="brand-dot"></span><span>Lumavento</span></div>
    <p class="brand-tagline">indhold for nye læsere</p>
  </div>
</section>

<section class="card card-back" aria-label="Visitkort bagside">
  <svg class="back-disc" viewBox="0 0 680 400" aria-hidden="true">
    <circle cx="660" cy="160" r="310" fill="var(--paper)"/>
  </svg>

  <div class="colour-tabs" aria-hidden="true">
    <span class="tab-orange"></span>
    <span class="tab-lime"></span>
    <span class="tab-magenta"></span>
    <span class="tab-purple"></span>
  </div>

  <div class="contact">
    <h1 class="contact-name">Sigrid Halvorsen</h1>
    <p class="contact-title">Salgsdirektør</p>
    <p>Lindegårds Allé 18</p>
    <p>8000 Aarhus C</p>
    <p>Tlf. +45 31 42 67 90</p>
    <ul class="contact-lines">
      <li>
        <svg viewBox="0 0 16 16" aria-hidden="true"><circle cx="8" cy="8" r="8" fill="var(--lime)"/><path d="M5 4.5h2l.6 2-1.2.8a5 5 0 0 0 2.3 2.3l.8-1.2 2 .6v2a1 1 0 0 1-1 1A7 7 0 0 1 4 5.5a1 1 0 0 1 1-1z" fill="var(--ink)"/></svg>
        <span>+45 31 42 67 90</span>
      </li>
      <li>
        <svg viewBox="0 0 16 16" aria-hidden="true"><circle cx="8" cy="8" r="8" fill="var(--lime)"/><rect x="5.5" y="3.5" width="5" height="9" rx="1" fill="var(--ink)"/><rect x="6.3" y="4.6" width="3.4" height="5.6" fill="var(--lime)"/></svg>
        <span>+45 52 18 73 04</span>
      </li>
      <li>
        <svg viewBox="0 0 16 16" aria-hidden="true"><circle cx="8" cy="8" r="8" fill="var(--lime)"/><rect x="3.5" y="5" width="9" height="6.5" fill="var(--ink)"/><path d="M3.8 5.3 8 8.6l4.2-3.3" fill="none" stroke="var(--lime)" stroke-width="1"/></svg>
        <span>sh@lumavento.dk</span>
      </li>
      <li>
        <svg viewBox="0 0 16 16" aria-hidden="true"><circle cx="8" cy="8" r="8" fill="var(--lime)"/><circle cx="8" cy="8" r="4.5" fill="none" stroke="var(--ink)" stroke-width="1.2"/><path d="M3.5 8h9M8 3.5c-2 2.5-2 6.5 0 9M8 3.5c2 2.5 2 6.5 0 9" fill="none" stroke="var(--ink)" stroke-width="1"/></svg>
        <span>www.lumavento.dk</span>
      </li>
    </ul>
  </div>
</section>

</body>
</html>
```